Web Design for a Biotech Consulting Firm

We need a web site design for a new business based in Philadelphia called Verantel Dx. This is a consulting firm that will serve medical diagnostics industry, which is part of the life science/healthcare industry focusing on developing and marketing products that help in early detection, monitoring or management of diseases. Our consulting firm will help medical diagnostic companies to overcome key challenges in designing, evaluating and marketing new products.Our company name is Verantel Dx. Verantel is Latin word for "something" Dx represents diagnostics. The idea behind the name is that we help companies to transform the original, early product ideas ("nothing") into "something"; which is a product with full clinical utility that will help to improve health and well-being.The web site should use the visual feel of the logo (attached), be modern, simple and clean looking and represent creativity, innovation, scientific thinking and progress.
Updates

Wix Design is acceptable

Industry/Entity Type

Biotechnology

Coding

Coded - Design and coding required

Number of Pages Required

1 page

Font styles to use
Sans Serif

Requirements
Must have
• simple, clean look couple of pages
Should not have
• a lot of pages

```html
<!DOCTYPE html>
<html lang="en">
<head>
<meta charset="utf-8">
<title>Verantel Dx — Biotech Consulting Firm</title>
<link href="https://fonts.googleapis.com/css2?family=Montserrat:wght@400;500;600;700&display=swap" rel="stylesheet">
<style>
:root{
  --blue:#1f6fd6;
  --ink:#1b1b1b;
  --body:#444b55;
  --muted:#6d737b;
  --pale:#e8f0fa;
  --card-line:#e3e6ea;
  --footer:#1b3c54;
  --white:#ffffff;
}
*{margin:0;padding:0;box-sizing:border-box}
html,body{width:1200px;height:2989px;overflow:hidden}
body{font-family:'Montserrat',sans-serif;color:var(--body);background:var(--white);position:relative}
.abs{position:absolute}

/* hero */
.hero{position:absolute;left:0;top:0;width:1200px;height:706px;
  background:linear-gradient(100deg,#4a6f99 0%,#6b8db5 40%,#7f9ec2 65%,#556f8f 100%);
  clip-path:polygon(0 0,1200px 0,1200px 607px,0 706px)}
.hero-shade{position:absolute;inset:0;background:linear-gradient(180deg,rgba(20,40,70,.25),rgba(20,40,70,.05))}
.brand-frame{position:absolute;left:142px;top:23px;width:94px;height:93px}
.brand-frame span{position:absolute;background:var(--blue)}
.brand-name{position:absolute;left:155px;top:56px;font-size:22px;font-weight:500;color:var(--white);white-space:nowrap}
.nav{position:absolute;top:52px;left:505px;display:flex;height:34px;align-items:center}
.nav a{color:var(--white);text-decoration:none;font-size:15px;margin-right:46px;white-space:nowrap}
.nav a.active{background:var(--blue);padding:0 20px;height:34px;line-height:34px;margin-right:28px}
.hero-title{position:absolute;left:0;width:1200px;top:238px;text-align:center;font-size:56px;font-weight:600;color:var(--white);letter-spacing:.5px}
.hero-sub{position:absolute;left:0;width:1200px;top:318px;text-align:center;font-size:17px;line-height:26px;color:var(--white)}
.btn{position:absolute;background:var(--blue);color:var(--white);font-size:14px;text-align:center;text-decoration:none}

/* about */
.about-bg{position:absolute;left:0;top:600px;width:1200px;height:672px;background:var(--pale);z-index:-1}
.about-frame{position:absolute;left:142px;top:790px;width:417px;height:408px;border:3px solid var(--blue)}
.about-photo{position:absolute;left:189px;top:755px;width:410px;height:402px;background:linear-gradient(135deg,#dfeefa 0%,#8fc0e6 45%,#2f7fc4 75%,#0f3e6e 100%)}

.head{position:absolute;font-size:28px;font-weight:500;color:var(--ink);white-space:nowrap}
.head em{font-style:normal;color:var(--blue)}
.head-mark{position:absolute;width:62px;height:64px}
.head-mark::before{content:"";position:absolute;left:0;top:0;width:100%;height:100%;border:2px solid var(--blue);border-right:none}
.head-mark::after{content:"";position:absolute;right:0;top:0;width:2px;height:9px;background:var(--blue);box-shadow:0 55px 0 var(--blue)}

.about-text{position:absolute;left:643px;top:906px;width:420px;font-size:14px;line-height:25.5px;color:var(--ink)}

/* services */
.card{position:absolute;top:1451px;width:218px;height:260px;border:1.5px solid var(--card-line);background:var(--white);text-align:center}
.card .ico{position:absolute;left:74px;top:45px;width:70px;height:70px;border:1.5px solid var(--blue)}
.card h3{position:absolute;left:0;width:100%;top:138px;font-size:15.5px;font-weight:500;color:var(--ink)}
.card p{position:absolute;left:12px;right:12px;top:166px;font-size:11px;line-height:18px;color:var(--muted)}

/* reviews */
.reviews{position:absolute;left:0;top:1781px;width:1200px;height:480px;background:linear-gradient(120deg,#c7d9ee 0%,#dbe7f4 45%,#eef3f9 70%,#d5e2f0 100%)}
.rev{position:absolute;top:2005px;width:294px;height:185px;background:rgba(255,255,255,.92);text-align:center}
.rev p{position:absolute;left:10px;right:10px;top:62px;font-size:12px;line-height:19px;letter-spacing:-.1px;color:var(--body)}
.rev b{position:absolute;left:0;width:100%;top:146px;font-weight:600;font-size:15px;color:var(--blue)}
.avatar{position:absolute;top:1968px;width:81px;height:81px;border:2px solid var(--blue);background:linear-gradient(180deg,#b9c8d8,#40536b)}
.arrow{position:absolute;width:25px;height:25px;border:1.5px solid var(--blue)}
.arrow svg{display:block}
.arrow.grey{border-color:#8a8f96}

/* partners */
.partner{position:absolute;top:2449px;width:210px;height:119px;background:var(--white);box-shadow:0 4px 14px rgba(0,0,0,.08);display:flex;align-items:center;justify-content:center;gap:10px;font-size:24px;font-weight:600;color:var(--ink)}
.partner i{display:block;width:32px;height:32px;border-radius:50%;background:var(--blue)}

/* footer */
.footer{position:absolute;left:0;top:2651px;width:1200px;height:338px;background:radial-gradient(circle at 30% 40%,#24506e 0%,var(--footer) 60%)}
.f-brand-name{position:absolute;left:154px;top:2741px;font-size:18px;font-weight:500;color:var(--white)}
.f-text{position:absolute;left:142px;top:2800px;width:200px;font-size:12px;line-height:19px;color:var(--white)}
.f-head{position:absolute;top:2710px;font-size:16px;font-weight:600;color:var(--blue)}
.f-list{position:absolute;list-style:none;font-size:12.5px;color:var(--white)}
.f-list li{height:25.5px}
.f-info{position:absolute;left:670px;font-size:12.5px;line-height:19px;color:var(--white);display:flex;gap:10px}
.f-info svg{flex:none;margin-top:2px}
.f-rule{position:absolute;left:142px;top:2895px;width:916px;height:1px;background:rgba(255,255,255,.18)}
.copy{position:absolute;left:0;width:1200px;top:2923px;text-align:center;font-size:11.5px;color:#c9d3dc}
.copy b{color:var(--white);font-weight:600}
</style>
</head>
<body>

<!-- HERO -->
<div class="hero" role="img" aria-label="Photo of a scientist in a lab coat studying digital medical scans">
  <div class="hero-shade"></div>
</div>

<div class="brand-frame">
  <span style="left:0;top:0;width:94px;height:2px"></span>
  <span style="left:0;top:0;width:2px;height:93px"></span>
  <span style="left:0;top:91px;width:94px;height:2px"></span>
  <span style="left:92px;top:0;width:2px;height:9px"></span>
  <span style="left:92px;top:82px;width:2px;height:11px"></span>
</div>
<div class="brand-name">Verantel Dx</div>

<nav class="nav">
  <a class="active" href="#">Home</a>
  <a href="#">About Us</a>
  <a href="#">Services</a>
  <a href="#">Innovations</a>
  <a href="#" style="margin-right:0">Contact Us</a>
</nav>

<h1 class="hero-title">Biotech Consulting Firm</h1>
<p class="hero-sub">We Will Serve Medical Diagnostics Industry, Which Is Part Of The<br>Life Science/healthcare Industry.</p>
<a class="btn" href="#" style="left:550px;top:407px;width:128px;height:36px;line-height:36px">Read More</a>

<!-- ABOUT -->
<div class="about-bg"></div>
<div class="about-frame"></div>
<div class="about-photo" role="img" aria-label="Photo of a gloved hand holding a flask of blue liquid with a pipette"></div>

<div class="head-mark" style="left:643px;top:812px"></div>
<h2 class="head" style="left:669px;top:826px">About <em>Verantel Dx</em></h2>
<p class="about-text">We are a Biotech consulting firm and we will serve medical diagnostics industry, which is part of the life science/healthcare industry focusing on developing and marketing products that help in early detection, monitoring or management of diseases.</p>
<a class="btn" href="#" style="left:643px;top:1071px;width:130px;height:37px;line-height:37px">Read More</a>

<!-- SERVICES -->
<div class="head-mark" style="left:506px;top:1343px"></div>
<h2 class="head" style="left:529px;top:1356px">Our <em>Services</em></h2>

<div class="card" style="left:142px">
  <div class="ico"><svg width="67" height="67" viewBox="0 0 67 67" fill="none" stroke="#333" stroke-width="1.6"><rect x="19" y="20" width="30" height="22" rx="3"/><circle cx="28" cy="29" r="3"/><path d="M24 42v8M30 42v8M40 26h5M40 32h5"/></svg></div>
  <h3>Corporate Strategy</h3>
  <p>Lorem Ipsum is simply dummy text of the printing and typesetting industry.</p>
</div>
<div class="card" style="left:374px">
  <div class="ico"><svg width="67" height="67" viewBox="0 0 67 67" fill="none" stroke="#333" stroke-width="1.6"><path d="M20 18h18l8 8v22H20z"/><path d="M25 32h14M25 38h10M25 44h10"/><circle cx="44" cy="44" r="5"/></svg></div>
  <h3>Product Development</h3>
  <p>Lorem Ipsum is simply dummy text of the printing and typesetting industry.</p>
</div>
<div class="card" style="left:606px">
  <div class="ico"><svg width="67" height="67" viewBox="0 0 67 67" fill="none" stroke="#333" stroke-width="1.6"><circle cx="34" cy="22" r="7"/><path d="M34 18v8"/><path d="M16 38l8-6 8 5 6-4 10 5-6 8-8-4-6 4z"/></svg></div>
  <h3>Business Development</h3>
  <p>Lorem Ipsum is simply dummy text of the printing and typesetting industry.</p>
</div>
<div class="card" style="left:840px">
  <div class="ico"><svg width="67" height="67" viewBox="0 0 67 67" fill="none" stroke="#333" stroke-width="1.6"><rect x="30" y="18" width="18" height="16"/><path d="M36 18v16M42 18v16"/><circle cx="26" cy="32" r="6"/><path d="M20 44h10v6H20z"/></svg></div>
  <h3>Commercialization</h3>
  <p>Lorem Ipsum is simply dummy text of the printing and typesetting industry.</p>
</div>

<!-- REVIEWS -->
<div class="reviews" role="img" aria-label="Soft blurred photo of a hand touching floating medical icons"></div>
<div class="head-mark" style="left:468px;top:1853px"></div>
<h2 class="head" style="left:492px;top:1866px">Customer <em>Reviews</em></h2>

<div class="rev" style="left:142px"><p>Lorem ipsum dolor sit amet, consectetuer adipiscing elit, sed diam nonummy nibh euismod tincidunt ut laoreet dolore magna aliquam erat volutpat.</p><b>Clara</b></div>
<div class="rev" style="left:453px"><p>Lorem ipsum dolor sit amet, consectetuer adipiscing elit, sed diam nonummy nibh euismod tincidunt ut laoreet dolore magna aliquam erat volutpat.</p><b>Clara</b></div>
<div class="rev" style="left:765px"><p>Lorem ipsum dolor sit amet, consectetuer adipiscing elit, sed diam nonummy nibh euismod tincidunt ut laoreet dolore magna aliquam erat volutpat.</p><b>Clara</b></div>
<div class="avatar" style="left:248px" role="img" aria-label="Portrait photo of a reviewer"></div>
<div class="avatar" style="left:560px" role="img" aria-label="Portrait photo of a reviewer"></div>
<div class="avatar" style="left:871px" role="img" aria-label="Portrait photo of a reviewer"></div>

<div class="arrow grey" style="left:81px;top:2083px"><svg width="22" height="22" viewBox="0 0 22 22"><path d="M13 6l-5 5 5 5" fill="none" stroke="#8a8f96" stroke-width="1.4"/></svg></div>
<div class="arrow" style="left:1094px;top:2083px"><svg width="22" height="22" viewBox="0 0 22 22"><path d="M9 6l5 5-5 5" fill="none" stroke="#1f6fd6" stroke-width="1.4"/></svg></div>

<!-- PARTNERS -->
<div class="head-mark" style="left:502px;top:2332px"></div>
<h2 class="head" style="left:526px;top:2345px">Our <em>Partners</em></h2>

<div class="partner" style="left:142px">Kestra<i></i></div>
<div class="partner" style="left:377px"><i></i>Orbiq</div>
<div class="partner" style="left:612px">Lumeno<i></i></div>
<div class="partner" style="left:847px"><i></i>Hexaro</div>

<div class="arrow grey" style="left:81px;top:2510px"><svg width="22" height="22" viewBox="0 0 22 22"><path d="M13 6l-5 5 5 5" fill="none" stroke="#8a8f96" stroke-width="1.4"/></svg></div>
<div class="arrow" style="left:1094px;top:2510px"><svg width="22" height="22" viewBox="0 0 22 22"><path d="M9 6l5 5-5 5" fill="none" stroke="#1f6fd6" stroke-width="1.4"/></svg></div>

<!-- FOOTER -->
<footer class="footer" role="img" aria-label="Dark blue microscopic cell imagery"></footer>
<div class="abs" style="left:142px;top:2714px;width:77px;height:76px">
  <div style="position:absolute;inset:0;border:2px solid var(--blue);border-right:none"></div>
  <div style="position:absolute;right:0;top:0;width:2px;height:8px;background:var(--blue)"></div>
  <div style="position:absolute;right:0;bottom:0;width:2px;height:9px;background:var(--blue)"></div>
</div>
<div class="f-brand-name">Verantel Dx</div>
<p class="f-text">Lorem ipsum dolor sit amet, consectetuer adipiscing elit, sed diam.</p>

<div class="f-head" style="left:453px">Quick Links</div>
<ul class="f-list" style="left:453px;top:2752px">
  <li>Home</li><li>About Us</li><li>Services</li><li>Innovations</li><li>Contact Us</li>
</ul>

<div class="f-head" style="left:670px">Our Information</div>
<div class="f-info" style="top:2753px"><svg width="12" height="15" viewBox="0 0 12 15"><path d="M6 0a6 6 0 0 0-6 6c0 4.5 6 9 6 9s6-4.5 6-9a6 6 0 0 0-6-6zm0 8.3a2.3 2.3 0 1 1 0-4.6 2.3 2.3 0 0 1 0 4.6z" fill="#fff"/></svg><span>48210 Lorem ipsum dolar<br>met ulorem, 5521</span></div>
<div class="f-info" style="top:2808px"><svg width="14" height="14" viewBox="0 0 14 14"><path d="M3 0l3 3-2 2c1 2 3 4 5 5l2-2 3 3-2 3C6 14 0 8 0 2z" fill="#fff"/></svg><span>+11 987 654 321</span></div>
<div class="f-info" style="top:2844px"><svg width="15" height="11" viewBox="0 0 15 11"><rect width="15" height="11" rx="1" fill="#fff"/><path d="M0 1l7.5 5L15 1" fill="none" stroke="#1b3c54" stroke-width="1.3"/></svg><span>info@veranteldx.com</span></div>

<div class="f-head" style="left:966px">Follow Us</div>
<div class="f-info" style="left:966px;top:2755px;align-items:center"><svg width="12" height="12"><circle cx="6" cy="6" r="5" fill="#fff"/></svg><span>Friendline</span></div>
<div class="f-info" style="left:966px;top:2786px;align-items:center"><svg width="12" height="12"><circle cx="6" cy="6" r="5" fill="#fff"/></svg><span>Chirpnet</span></div>

<div class="f-rule"></div>
<p class="copy">© 2019 <b>Verantel Dx.</b> All rights reserved.</p>

</body>
</html>
```